Fresh and unique Mortgage Broking business needs website design.

We need a professional yet fresh, bright and colourful website for my Mortgage broking business.
We specialise in the Non conforming/sub prime market with clients who have been rejected by other banks or have trouble getting finance through a traditional lender.
We are called Lark Lending and we aim to provide Hope to our clients when they have thought there was no hope.
I would like it to be on a Wordpress platform as I plan to do a lot of postings, both written and video and I need it to be easy to use.
I would also like it to be able to have a clear and simple enquiry box on the first page to capture contact details and notify me via email.

I have already had the logo designed in both green and black and a white version.
I have also had a a header made up using the white logo with leaves background that could possibly be used as the website header which I have used as my facebook header.

https://www.pagebook-example.com/MarcusDellowLark/

I tried playing around with a sitebuild website builder which kind of got some of the brightness and colours I was after but it had a lot to go.

http://larklending.sitebuildexample.com/

Industry/Entity Type

Finance

Number of Pages Required

4 page

Colors
0292cd
00a990
fbed22
ffc214
f78f20
ec1f27

Requirements
Nice to have
• I'm not sure what the difference between uncoded and coded website is so I'm not sure what I need?

```html
<!DOCTYPE html>
<html lang="en">
<head>
<meta charset="utf-8">
<title>Lark Lending</title>
<link href="https://fonts.googleapis.com/css2?family=Lora:ital,wght@0,400;0,700;1,400&family=Open+Sans:ital,wght@0,400;0,600;0,700;1,400&display=swap" rel="stylesheet">
<style>
:root{
  --orange:#f78f20;
  --teal:#00a38a;
  --blue:#0292cd;
  --yellow:#ffc214;
  --red:#ec1f27;
  --green:#1f8a4c;
  --ink:#1d1d1d;
  --text:#666;
  --line:#e3e3e3;
  --band:#f2f4f5;
  --white:#fff;
}
*{box-sizing:border-box;margin:0;padding:0}
html,body{width:1200px;height:2359px;overflow:hidden;background:var(--white)}
body{font-family:"Open Sans",sans-serif;color:var(--text);font-size:13px;line-height:1.75}
.wrap{width:1004px;margin:0 auto;position:relative}
h1,h2,h3,.serif{font-family:"Lora",serif;color:var(--ink)}
a{color:inherit;text-decoration:none}

/* hero */
.hero{height:560px;position:relative;overflow:hidden}
.hero-photo{position:absolute;inset:0;background:
  radial-gradient(ellipse 420px 300px at 820px 250px,#d9601c 0%,rgba(217,96,28,0) 70%),
  radial-gradient(ellipse 380px 260px at 280px 330px,#a88a1f 0%,rgba(168,138,31,0) 75%),
  radial-gradient(ellipse 300px 240px at 1100px 120px,#1b0b05 0%,rgba(27,11,5,0) 80%),
  linear-gradient(100deg,#6b3a12 0%,#9a6a1e 30%,#c25a1a 55%,#7a2410 78%,#2a0c06 100%)}
.topbar{position:absolute;top:0;left:0;right:0}
.topbar .wrap{display:flex;justify-content:space-between;align-items:center;height:100px}
.brand{font-family:"Lora",serif;font-size:30px;font-weight:700;color:var(--white);letter-spacing:.5px}
.nav{display:flex;gap:0;align-items:center}
.nav a{font-family:"Lora",serif;font-weight:700;font-size:14px;color:var(--white);margin-left:50px;letter-spacing:.3px}
.nav svg{margin-left:50px}
.hero-copy{position:absolute;left:98px;top:218px;width:620px}
.hero-copy h1{color:var(--white);font-size:52px;font-weight:700;letter-spacing:.5px;line-height:1.1}
.hero-copy p{color:var(--white);font-size:18px;font-weight:600;line-height:1.65;margin-top:22px}
.btn-outline{display:inline-block;border:1.5px solid var(--white);border-radius:4px;color:var(--white);font-weight:700;font-size:15px;padding:8px 29px;margin-top:30px}
.dots{position:absolute;left:534px;top:506px;display:flex;gap:4px}
.dots span{width:31px;height:4px;border:1px solid var(--white);border-radius:2px}
.dots span.on{background:var(--white)}

/* about */
.about{height:385px;padding-top:52px}
.about .wrap{display:flex;justify-content:space-between}
.about-copy{width:500px}
.about-copy h2{font-size:23px;font-weight:700;line-height:1.5;text-transform:uppercase}
.about-copy p{margin-top:18px;font-size:12.5px}
.btn-small{display:inline-block;border:1px solid #999;color:var(--orange);font-weight:700;font-size:12px;padding:6px 17px;margin-top:22px}
.video{width:466px;height:278px;border:1px solid #ccc;padding:4px;box-shadow:0 1px 3px rgba(0,0,0,.15)}
.video-photo{width:100%;height:100%;position:relative;background:linear-gradient(120deg,#6d7a56 0%,#c9c3a6 35%,#e7dfd1 55%,#7fa04a 100%)}
.video-photo .play{position:absolute;left:50%;top:50%;transform:translate(-50%,-50%)}

/* services */
.services{height:405px;background:var(--band);padding-top:45px}
.services h2{text-align:center;font-size:23px;font-weight:700}
.svc-grid{display:grid;grid-template-columns:362px 362px 280px;row-gap:32px;margin-top:22px}
.svc{display:flex;gap:20px}
.svc-icon{width:48px;flex:none;padding-top:2px}
.svc h3{font-size:17.5px;font-weight:700;line-height:1.4}
.svc p{font-size:12px;line-height:1.85;margin-top:4px;width:220px}

/* why + blog */
.split{height:485px;padding-top:50px}
.split .wrap{display:flex;justify-content:space-between}
.why{width:452px}
.split h2{font-size:23px;font-weight:700;text-transform:uppercase}
.why .intro{font-size:12px;margin-top:22px;line-height:1.7}
.ticks{list-style:none;margin-top:14px}
.ticks li{display:flex;align-items:center;gap:14px;font-size:12px;height:38.5px}
.more{display:block;color:var(--orange);font-weight:700;font-size:12px;margin-top:14px}
.blog{width:516px}
.post{display:flex;gap:20px;padding:24px 0 20px;border-bottom:1px solid var(--line)}
.post+.post{padding-top:18px}
.thumb{width:156px;height:120px;border:1px solid #ccc;padding:3px;flex:none}
.thumb div{width:100%;height:100%}
.t1{background:linear-gradient(160deg,#5fc3e6 0%,#f2e96a 55%,#e6d6b9 100%)}
.t2{background:linear-gradient(180deg,#7ab6e6 0%,#d5e7f3 50%,#c89a7a 100%)}
.post h3{font-family:"Open Sans",sans-serif;font-size:13.5px;font-weight:700;text-decoration:underline;line-height:1.5}
.meta{display:flex;gap:16px;font-style:italic;font-size:11px;color:#888;margin-top:6px}
.meta span{display:flex;align-items:center;gap:5px}
.post p{font-size:11.8px;margin-top:4px;line-height:1.8}

/* testimonial */
.quote{height:210px;background:var(--teal);position:relative}
.quote .arrow{position:absolute;top:88px}
.quote .wrap{display:flex;align-items:center;height:210px}
.avatar{width:130px;height:130px;border-radius:50%;border:4px solid var(--white);background:radial-gradient(circle at 50% 40%,#c9b8a8,#6f7f86);margin-left:12px;flex:none}
.quote .rule{width:1px;height:160px;background:rgba(255,255,255,.6);margin:0 32px 0 36px}
.quote blockquote{color:var(--white);font-style:italic;font-size:14.5px;line-height:1.85;width:770px}
.quote cite{display:block;font-family:"Lora",serif;font-style:normal;font-weight:700;font-size:18px;margin-top:14px}

/* footer */
.footer{height:314px;padding-top:46px}
.foot-cols{display:flex;height:210px}
.foot-brand{width:328px;padding-top:70px;font-family:"Lora",serif;font-size:38px;font-weight:700;color:var(--green)}
.foot-col h4{font-family:"Lora",serif;font-weight:700;font-size:16px;color:var(--ink);margin-bottom:10px}
.info{width:170px}
.info li{list-style:none;font-size:12px;line-height:29px}
.news{width:305px}
.news p{font-size:12px;line-height:1.75}
.field{width:254px;height:36px;background:#eee;border-bottom:1px solid #ccc;margin-top:10px;padding:7px 14px;color:#999;font-size:12px}
.btn-sub{display:inline-block;border:1px solid #999;color:var(--orange);font-weight:700;font-size:11px;padding:4px 12px;margin-top:14px}
.contact li{list-style:none;display:flex;align-items:center;gap:18px;font-size:12px;height:36px}
.bottom{border-top:1px solid var(--line);display:flex;justify-content:space-between;align-items:center;height:58px;font-size:12px}
.social{display:flex;gap:10px}
.social span{width:26px;height:26px;border:1.5px solid var(--orange);border-radius:50%}
</style>
</head>
<body>

<header class="hero">
  <div class="hero-photo" role="img" aria-label="Close-up of orange autumn maple leaves against a soft green and red background"></div>
  <div class="topbar">
    <div class="wrap">
      <div class="brand">Lark Lending</div>
      <nav class="nav">
        <a href="#">HOME</a><a href="#">ABOUT</a><a href="#">SERVICES</a><a href="#">PROPERTY ADVICE</a><a href="#">CONTACT</a>
        <svg width="14" height="14" viewBox="0 0 14 14"><circle cx="5.8" cy="5.8" r="4.3" fill="none" stroke="#fff" stroke-width="2"/><line x1="9" y1="9" x2="13" y2="13" stroke="#fff" stroke-width="2.2" stroke-linecap="round"/></svg>
      </nav>
    </div>
  </div>
  <div class="hero-copy">
    <h1>LARK LENDING</h1>
    <p>We specialise in the Non conforming/sub prime market with clients who have been rejected by other banks or have trouble getting finance through a traditional lender.</p>
    <a class="btn-outline" href="#">GET A QUOTE</a>
  </div>
  <div class="dots"><span class="on"></span><span></span><span></span><span></span></div>
</header>

<section class="about">
  <div class="wrap">
    <div class="about-copy">
      <h2>Hope for your finance when all hope is lost</h2>
      <p>Lark Lending is a Christian Mortgage Broking business. Marcus lives in Brookvale and loves exploring the Westridge Shire with his wife and kids for great places to eat.</p>
      <p>With over 10 years' experience in financial services ranging from insurance, superannuation, investments and finance, Marcus bringing together his experience to provide a more holistic approach to his customers.</p>
      <a class="btn-small" href="#">READ MORE &gt;&gt;</a>
    </div>
    <div class="video">
      <div class="video-photo" role="img" aria-label="Video still of a smiling family outside their new home">
        <svg class="play" width="56" height="56" viewBox="0 0 56 56"><circle cx="28" cy="28" r="26" fill="rgba(0,0,0,.55)" stroke="#fff" stroke-width="2.5"/><path d="M22 17 L39 28 L22 39 Z" fill="#fff"/></svg>
      </div>
    </div>
  </div>
</section>

<section class="services">
  <div class="wrap">
    <h2>OUR SERVICES</h2>
    <div class="svc-grid">
      <div class="svc">
        <svg class="svc-icon" viewBox="0 0 48 40" height="40"><path d="M24 3 L2 21 H8 V38 H19 V27 H29 V38 H40 V21 H46 Z" fill="var(--blue)"/></svg>
        <div><h3>Residential loans</h3><p>At vero eos et accusamus et iust odio dignissimos ducimus qui blanditiis pr aesentium voluptat.</p></div>
      </div>
      <div class="svc">
        <svg class="svc-icon" viewBox="0 0 58 44" height="44"><g fill="var(--yellow)"><rect x="0" y="0" width="3" height="44"/><rect x="0" y="41" width="58" height="3"/><rect x="9" y="22" width="7" height="17"/><rect x="19" y="14" width="7" height="25"/><rect x="29" y="24" width="7" height="15"/><rect x="39" y="10" width="7" height="29"/><rect x="49" y="18" width="7" height="21"/></g></svg>
        <div><h3>Investment loans</h3><p>At vero eos et accusamus et iust odio dignissimos ducimus qui blanditiis pr aesentium voluptat.</p></div>
      </div>
      <div class="svc">
        <svg class="svc-icon" viewBox="0 0 48 46" height="46"><circle cx="24" cy="12" r="11" fill="var(--teal)"/><path d="M4 46 V38 Q4 26 16 26 H32 Q44 26 44 38 V46 Z" fill="var(--teal)"/></svg>
        <div><h3>Self employed loans</h3><p>At vero eos et accusamus et iust odio dignissimos ducimus qui blanditiis pr aesentium voluptat.</p></div>
      </div>
      <div class="svc">
        <svg class="svc-icon" viewBox="0 0 52 46" height="46"><path d="M26 2 L51 44 H1 Z" fill="var(--red)" stroke="var(--red)" stroke-linejoin="round" stroke-width="2"/><rect x="23.5" y="15" width="5" height="16" rx="2" fill="#fff"/><circle cx="26" cy="37" r="3" fill="#fff"/></svg>
        <div><h3>Non confirming loans</h3><p>At vero eos et accusamus et iust odio dignissimos ducimus qui blanditiis pr aesentium voluptat.</p></div>
      </div>
      <div class="svc">
        <svg class="svc-icon" viewBox="0 0 48 48" height="48"><rect x="2" y="4" width="10" height="22" fill="var(--green)"/><path d="M14 4 H34 Q40 4 40 10 L42 24 Q42 28 38 28 H28 L30 40 Q30 46 25 44 L22 32 L14 26 Z" fill="var(--green)"/></svg>
        <div><h3>Bad credit &amp; Low doc</h3><p>At vero eos et accusamus et iust odio dignissimos ducimus qui blanditiis pr aesentium voluptat.</p></div>
      </div>
      <div class="svc">
        <svg class="svc-icon" viewBox="0 0 56 44" height="44"><rect x="2" y="2" width="52" height="40" rx="5" fill="none" stroke="var(--orange)" stroke-width="3"/><rect x="2" y="11" width="52" height="8" fill="var(--orange)"/><rect x="8" y="30" width="16" height="4" fill="var(--orange)"/></svg>
        <div><h3>Debt consolidation</h3><p>At vero eos et accusamus et iust odio dignissimos ducimus qui blanditiis pr aesentium voluptat.</p></div>
      </div>
    </div>
  </div>
</section>

<section class="split">
  <div class="wrap">
    <div class="why">
      <h2>Why choose us</h2>
      <p class="intro">At vero eos et accusamus et iusto odio dignissimos ducimus qui blanditii praese ntium voluptatum deleniti atque corrupti quos .</p>
      <ul class="ticks">
        <li><svg width="15" height="15" viewBox="0 0 16 16"><circle cx="8" cy="8" r="8" fill="var(--teal)"/><path d="M4.5 8.2 L7 10.6 L11.6 5.6" fill="none" stroke="#fff" stroke-width="2"/></svg>Blanditiis praesentium voluptatum deleniti atque corrupti quos</li>
        <li><svg width="15" height="15" viewBox="0 0 16 16"><circle cx="8" cy="8" r="8" fill="var(--teal)"/><path d="M4.5 8.2 L7 10.6 L11.6 5.6" fill="none" stroke="#fff" stroke-width="2"/></svg>Sed ut perspiciatis unde omnis iste natus error sit voluptatem accusanti</li>
        <li><svg width="15" height="15" viewBox="0 0 16 16"><circle cx="8" cy="8" r="8" fill="var(--teal)"/><path d="M4.5 8.2 L7 10.6 L11.6 5.6" fill="none" stroke="#fff" stroke-width="2"/></svg>But I must explain to you how all this mistaken idea of denouncing</li>
        <li><svg width="15" height="15" viewBox="0 0 16 16"><circle cx="8" cy="8" r="8" fill="var(--teal)"/><path d="M4.5 8.2 L7 10.6 L11.6 5.6" fill="none" stroke="#fff" stroke-width="2"/></svg>Nemo enim ipsam voluptatem quia voluptas sit aspernatur</li>
        <li><svg width="15" height="15" viewBox="0 0 16 16"><circle cx="8" cy="8" r="8" fill="var(--teal)"/><path d="M4.5 8.2 L7 10.6 L11.6 5.6" fill="none" stroke="#fff" stroke-width="2"/></svg>At vero eos et accusamus et iusto odio dignissimos ducimus qui</li>
        <li><svg width="15" height="15" viewBox="0 0 16 16"><circle cx="8" cy="8" r="8" fill="var(--teal)"/><path d="M4.5 8.2 L7 10.6 L11.6 5.6" fill="none" stroke="#fff" stroke-width="2"/></svg>Nam libero tempore, cum soluta nobis est eligendi optio cumque nihil</li>
      </ul>
      <a class="more" href="#">READ MORE &gt;&gt;</a>
    </div>
    <div class="blog">
      <h2>Our blog</h2>
      <article class="post">
        <div class="thumb"><div class="t1" role="img" aria-label="Couple smiling on a sunny beach holiday"></div></div>
        <div>
          <h3>AT VERO EOS ET ACCUSAMUS ET IUSTO ODIODIG NISSIMOS DUCIMUS QUI BLAND</h3>
          <div class="meta"><span>&#9635; 15/10/2015</span><span>&#9679; Sam Carter</span><span>&#9632; 4 Comments</span></div>
          <p>Duis aute irure dolor in reprehenderit in voluptate velit esse cillum dolore eu fugiat nulla pariatur.</p>
        </div>
      </article>
      <article class="post">
        <div class="thumb"><div class="t2" role="img" aria-label="Cupped hands holding a small model house"></div></div>
        <div>
          <h3>AT VERO EOS ET ACCUSAMUS ET IUSTO ODIODIG NISSIMOS DUCIMUS QUI BLAND</h3>
          <div class="meta"><span>&#9635; 15/10/2015</span><span>&#9679; Sam Carter</span><span>&#9632; 4 Comments</span></div>
          <p>Duis aute irure dolor in reprehenderit in voluptate velit esse cillum dolore eu fugiat nulla pariatur.</p>
        </div>
      </article>
      <a class="more" href="#">VIEW MORE &gt;&gt;</a>
    </div>
  </div>
</section>

<section class="quote">
  <svg class="arrow" style="left:34px" width="20" height="34" viewBox="0 0 20 34"><path d="M17 3 L4 17 L17 31" fill="none" stroke="rgba(255,255,255,.75)" stroke-width="3"/></svg>
  <svg class="arrow" style="right:34px" width="20" height="34" viewBox="0 0 20 34"><path d="M3 3 L16 17 L3 31" fill="none" stroke="rgba(255,255,255,.75)" stroke-width="3"/></svg>
  <div class="wrap">
    <div class="avatar" role="img" aria-label="Portrait of the client giving the testimonial"></div>
    <div class="rule"></div>
    <blockquote>Nam libero tempore, cum soluta nobis est eligendi optio cumque nihil impedit quo minus id quod maxime placeat facere possimus, omnis voluptas assumenda est, omnis dolor repellendus. Temporibus autem quibusdam et aut officiis debitis aut rerum necessitatibus saepe eveniet ut et voluptates repudiandae sint et molestiae
      <cite>- Elise Marrow</cite>
    </blockquote>
  </div>
</section>

<footer class="footer">
  <div class="wrap">
    <div class="foot-cols">
      <div class="foot-brand">Lark Lending</div>
      <div class="foot-col info">
        <h4>Information</h4>
        <ul><li>Home</li><li>About</li><li>Services</li><li>Property Advice</li><li>Contact</li></ul>
      </div>
      <div class="foot-col news">
        <h4>Newsletter Subscription</h4>
        <p>Register your Email Address to get<br>information about us</p>
        <div class="field">Email Address</div>
        <a class="btn-sub" href="#">SUBSCRIBE</a>
      </div>
      <div class="foot-col contact">
        <h4>Contact Us</h4>
        <ul>
          <li><svg width="12" height="14" viewBox="0 0 12 16"><path d="M6 0 A6 6 0 0 1 12 6 C12 10 6 16 6 16 C6 16 0 10 0 6 A6 6 0 0 1 6 0Z" fill="var(--orange)"/><circle cx="6" cy="6" r="2.2" fill="#fff"/></svg>PO Box 218 Brookvale VIC 3899</li>
          <li><svg width="12" height="14" viewBox="0 0 16 16"><path d="M3 1 L6 1 L7 5 L5 6.5 Q6.5 9.5 9.5 11 L11 9 L15 10 L15 13 Q15 15 13 15 Q1 14 1 3 Q1 1 3 1Z" fill="var(--orange)"/></svg>0400 512 377</li>
          <li><svg width="12" height="14" viewBox="0 0 16 16"><rect x="1" y="6" width="14" height="9" rx="1" fill="var(--orange)"/><rect x="4" y="1" width="8" height="6" fill="var(--orange)"/><rect x="4" y="9" width="8" height="2" fill="#fff"/></svg>(03) 9010 2244</li>
          <li><svg width="12" height="14" viewBox="0 0 16 12"><rect x="0" y="0" width="16" height="12" rx="1" fill="var(--orange)"/><path d="M0 1 L8 7 L16 1" fill="none" stroke="#fff" stroke-width="1.3"/></svg>marcus@larklending.example</li>
        </ul>
      </div>
    </div>
    <div class="bottom">
      <span>Copyrights © 2016, Lark Lending. All rights reserved.</span>
      <div class="social"><span></span><span></span><span></span><span></span></div>
    </div>
  </div>
</footer>

</body>
</html>
```